Design a poster that illustrates the six central pillars of our school district's efforts with students. The attached PDF outlines the six main competencies we aim for students to possess upon graduation. Each of the 6 has 3 bullet points for the poster as well. The title is "Profile of a Trailblazer". Our mascot is this attached winged wheel. The overall concept is that staff take kids when they are young and develop these 6 things when they graduate. Our colors are navy, red, and white. We will make this poster in a variety of sizes in offices, classrooms, and in digital spaces as well. On the PDF - ignore the column that says "Synthesis". That has nothing to do with this poster.

The district is Harlow Creek Public Schools https://www.harlowcreek-schools.example/

```html
<!DOCTYPE html>
<html lang="en">
<head>
<meta charset="utf-8">
<title>Profile of a Trailblazer</title>
<link href="https://fonts.googleapis.com/css2?family=Bubblegum+Sans&family=Exo+2:wght@300&family=Archivo+Black&display=swap" rel="stylesheet">
<style>
  :root {
    --navy: #0c0e3a;
    --red: #a31e25;
    --white: #ffffff;
    --ink: #23232f;
    --blue: #00aeef;
    --crimson: #e8333c;
    --green: #00a651;
    --orange: #f5923e;
    --lavender: #a19ccf;
  }
  html, body { margin: 0; padding: 0; overflow: hidden; }
  body { width: 884px; height: 1200px; background: var(--navy); position: relative; }
  .poster {
    position: absolute; left: 67px; top: 60px; width: 750px; height: 1081px;
    box-sizing: border-box; border: 11px solid var(--red); border-radius: 38px;
    background: var(--white); overflow: hidden;
  }
  .district {
    position: absolute; left: 0; right: 0; top: 118px; display: flex;
    justify-content: center; align-items: center; gap: 12px;
    font-family: "Bubblegum Sans", cursive; font-size: 30px; color: var(--navy);
  }
  .district .dot { width: 34px; height: 34px; border-radius: 50%; background: var(--red); }
  .title-band {
    position: absolute; left: 0; right: 0; top: 175px; height: 71px; background: var(--red);
    display: flex; align-items: center; justify-content: center; color: var(--white);
    font-size: 50px; white-space: nowrap;
  }
  .title-band .lead { font-family: "Exo 2", sans-serif; font-weight: 300; margin-right: 14px; }
  .title-band .key { font-family: "Archivo Black", sans-serif; letter-spacing: 1px; }
  .path-lines { position: absolute; left: 0; top: 0; }
  .mark {
    position: absolute; display: flex; align-items: center; gap: 5px;
    font-family: "Bubblegum Sans", cursive; font-size: 14px; color: var(--navy);
  }
  .mark .dot { width: 16px; height: 16px; border-radius: 50%; background: var(--navy); }
  .pillar-name {
    position: absolute; font-family: "Bubblegum Sans", cursive; font-size: 25px;
    line-height: 1; white-space: nowrap;
  }
  .traits {
    position: absolute; left: 157px; margin: 0; padding: 0; list-style: none;
    font-family: "Bubblegum Sans", cursive; font-size: 18.5px; color: var(--ink); line-height: 21.5px;
  }
  .traits li { position: relative; padding-left: 12px; white-space: nowrap; }
  .traits li::before { content: "•"; position: absolute; left: 0; }
</style>
</head>
<body>
  <div class="poster">
    <div class="district"><span class="dot"></span>Harlow Creek Public Schools</div>
    <div class="title-band"><span class="lead">Profile of a</span><span class="key">TRAILBLAZER</span></div>
  </div>

  <svg class="path-lines" width="884" height="1200" viewBox="0 0 884 1200" fill="none" stroke-width="4">
    <path stroke="var(--blue)" d="M209 408 H532 M685 408 H703 A51 53 0 0 1 703 514 H332"/>
    <path stroke="var(--crimson)" d="M172 514 H168 A51 52 0 0 0 168 618 H530"/>
    <path stroke="var(--green)" d="M662 618 H703 A51 52 0 0 1 703 722 H281"/>
    <path stroke="var(--orange)" d="M172 722 H168 A51 58.5 0 0 0 168 839 H530"/>
    <path stroke="var(--crimson)" d="M669 839 H703 A51 52.5 0 0 1 703 944 H332"/>
    <path stroke="var(--lavender)" d="M172 944 H168 A51 53 0 0 0 168 1050 H626"/>
  </svg>

  <div class="mark" style="left:134px; top:372px;"><span class="dot"></span>Harlow Creek</div>
  <div class="mark" style="left:642px; top:1048px;"><span class="dot"></span>Harlow Creek</div>

  <div class="pillar-name" style="left:539px; top:396px; color:var(--blue);">Communicator</div>
  <ul class="traits" style="top:425px;">
    <li>Expresses ideas clearly &nbsp;and respectfully (written &amp; verbal).</li>
    <li>Listens actively and understands diverse perspectives.</li>
    <li>Adjusts communication to suit the audience and context.</li>
  </ul>

  <div class="pillar-name" style="left:179px; top:502px; color:var(--crimson);">Critical Thinker</div>
  <ul class="traits" style="top:531px; line-height:19.8px;">
    <li>Questions, analyzes, and evaluates information from multiple sources.</li>
    <li>Identifies and solves complex problems creatively.</li>
    <li>Uses evidence and diverse perspectives to form reasoned conclusions<br>and make informed decisions</li>
  </ul>

  <div class="pillar-name" style="left:539px; top:606px; color:var(--green);">Responsible</div>
  <ul class="traits" style="top:643px;">
    <li>Takes ownership of actions, choices, and commitments.</li>
    <li>Manages time, resources, and self to meet expectations.</li>
    <li>Acts with integrity and advocates for self and others.</li>
  </ul>

  <div class="pillar-name" style="left:179px; top:710px; color:var(--orange);">Adaptable</div>
  <ul class="traits" style="top:743px; letter-spacing:-0.3px;">
    <li>Responds productively to new situations, challenges, and feedback.</li>
    <li>Learns from new experiences and applies prior knowledge in evolving contexts.</li>
    <li>Adjusts behavior and approach to effectively engage with<br>diverse groups and &nbsp;environments.</li>
  </ul>

  <div class="pillar-name" style="left:539px; top:827px; color:var(--crimson);">Collaborator</div>
  <ul class="traits" style="top:862px;">
    <li>Contributes effectively and cooperatively to shared goals</li>
    <li>Listens actively and values diverse ideas and perspectives.</li>
    <li>Engages respectfully, compromising and leading when appropriate</li>
  </ul>

  <div class="pillar-name" style="left:179px; top:932px; color:var(--lavender);">Compassionate</div>
  <ul class="traits" style="top:965px; line-height:24.5px; letter-spacing:-0.2px;">
    <li>Understands and acknowledges others' feelings, perspectives, and experiences.</li>
    <li>Responds with kindness, patience, and support.</li>
    <li>Seeks to connect with and contribute positively to the well-being of others</li>
  </ul>
</body>
</html>
```